Stationary Design for Quince consultant and support company

We need new stationary designed for a London based support company that provide on-site and remote support services for Quince products. Our clients are both consumers and businesses.

We would like a letterhead, compliment slip, business card and possibly an e-mail signature designed.

Business card designs can be either 1 side or 2, depending on designs we receive we may choose a preference for 1 or 2 sides later on in the design stage.

Designs needs to be at least 300dpi and should be done using CMYK colours.

We want the design to be bold, easy to read, clean and professional.

We have attached our company logo in 2 colour variations (if you need any other source files then please ask).

Our logo colours are as follows:

Blue (85, 50, 0, 0) and Green (50, 0, 100, 0)

We use two different suppliers for out stationary so here are the size dimensions for both. Unfortunately they are ever so slightly different size wise so hopefully we can get something that accommodates both, we can provide dimensions if required for final versions.

Some fonts that have been used before with our company are Probert (for tagline on our company logo) and previously had Nauman used, however we are very much open to seeing what the designers come up with and the fonts mentioned are not a requirement.
Updates

Company details for designs (however the template should be editable for multiple staff) Lumora Ltd. Registered Office: 62-70 Harrowfield Lane London N7 3QD 020 7591 3384 www.lumora-it.example info@lumora-it.example Company is Registered in England and Wales Company No. 07342519 Directors details (if you want to make the template using his details), rest of the details are as above Dan Frost Director dan@lumora-it.example

Hi all, Thank you for your submissions so far. Could we please ask that you don't use the logo with the tagline from our website for the stationary designs and only the logos provided in the design brief. For the business cards we are looking at normal rectangular business cards to be used and we can provide a template guide for size if needed, please just ask. Regards Lumora Team

Target Market(s)

Our target market are consumers (of all ages) and small/medium businesses.

Industry/Entity Type

Business

Font styles to use
Serif
Sans Serif

Requirements
Must have
• At least business card, letterhead and compliment slip submitted (we need all 3 designed this time round)
Should not have
• Business cards should not have the writing "registered office" (letterheads and compliment slips can along the bottom edge)

```html
<!DOCTYPE html>
<html lang="en">
<head>
<meta charset="utf-8">
<title>Lumora Business Cards</title>
<link href="https://fonts.googleapis.com/css2?family=Open+Sans:wght@400;600;800&display=swap" rel="stylesheet">
<style>
  :root {
    --bg: #e8e9ea;
    --brand-blue: #4377a9;
    --brand-green: #8cb654;
    --ink: #353535;
    --paper: #f7f7f7;
    --white: #ffffff;
  }
  * { margin: 0; padding: 0; box-sizing: border-box; }
  html, body { width: 1200px; height: 1000px; overflow: hidden; }
  body {
    background: var(--bg);
    font-family: "Open Sans", Arial, sans-serif;
    position: relative;
  }
  .card {
    position: absolute;
    width: 250px;
    height: 420px;
    border-radius: 2px;
    box-shadow: 0 2px 6px rgba(0,0,0,0.12);
  }
  .card--green { left: 330px; top: 70px; background: var(--brand-green); }
  .card--white { left: 330px; top: 510px; background: var(--paper); }
  .card--blue-dark-mark { left: 620px; top: 70px; background: var(--brand-blue); }
  .card--blue-light-mark { left: 620px; top: 510px; background: var(--brand-blue); }

  .wordmark {
    position: absolute;
    font-weight: 800;
    font-size: 30px;
    letter-spacing: 1px;
    text-transform: uppercase;
    color: var(--ink);
    display: flex;
    align-items: center;
    gap: 8px;
  }
  .wordmark__square { width: 12px; height: 12px; background: currentColor; }
  .card--green .wordmark,
  .card--white .wordmark { top: 60px; right: 30px; }
  .card--blue-dark-mark .wordmark,
  .card--blue-light-mark .wordmark { top: 150px; left: 50%; transform: translateX(-50%); }
  .card--blue-light-mark .wordmark { color: var(--white); }

  .contact {
    position: absolute;
    left: 28px;
    bottom: 34px;
  }
  .contact__name { font-size: 17px; font-weight: 600; line-height: 1.1; }
  .contact__role { font-size: 12px; margin-bottom: 8px; }
  .contact__list { list-style: none; font-size: 8px; line-height: 1.6; }
  .contact__list li { display: flex; align-items: center; gap: 5px; }
  .contact__bullet { width: 5px; height: 5px; display: inline-block; }

  .card--green .contact { color: var(--white); }
  .card--green .contact__role { color: #eef5e4; }
  .card--green .contact__bullet { background: var(--brand-blue); }

  .card--white .contact { color: var(--ink); }
  .card--white .contact__name { color: var(--brand-blue); }
  .card--white .contact__role { color: var(--brand-green); }
  .card--white .contact__bullet { background: var(--brand-green); }
</style>
</head>
<body>

  <section class="card card--green">
    <div class="wordmark"><span>Lumora</span><span class="wordmark__square"></span></div>
    <div class="contact">
      <p class="contact__name">Dan Frost</p>
      <p class="contact__role">Director</p>
      <ul class="contact__list">
        <li><span class="contact__bullet"></span>020 7591 3384</li>
        <li><span class="contact__bullet"></span>dan@lumora-it.example</li>
        <li><span class="contact__bullet"></span>www.lumora-it.example</li>
        <li><span class="contact__bullet"></span>London N7 3QD</li>
      </ul>
    </div>
  </section>

  <section class="card card--white">
    <div class="wordmark"><span>Lumora</span><span class="wordmark__square"></span></div>
    <div class="contact">
      <p class="contact__name">Dan Frost</p>
      <p class="contact__role">Director</p>
      <ul class="contact__list">
        <li><span class="contact__bullet"></span>020 7591 3384</li>
        <li><span class="contact__bullet"></span>dan@lumora-it.example</li>
        <li><span class="contact__bullet"></span>www.lumora-it.example</li>
        <li><span class="contact__bullet"></span>London N7 3QD</li>
      </ul>
    </div>
  </section>

  <section class="card card--blue-dark-mark">
    <div class="wordmark"><span>Lumora</span><span class="wordmark__square"></span></div>
  </section>

  <section class="card card--blue-light-mark">
    <div class="wordmark"><span>Lumora</span><span class="wordmark__square"></span></div>
  </section>

</body>
</html>
```